Corporate Design für Hotel/Restaurant
Zielgruppe
Unsere Kundschaft ist sehr breit gestreut. Unser CI sollte entsprechend die Ü60 jährigen, wie auch die ca. 30+ jährigen Kleinstädter ansprechen.
Aufgabenstellung
Es handelt sich um einen Familienbetrieb in zweiter Generation, der trotz altem deutschen Namen „Hotel-Restaurant zum Brunnenhof“ eine klare asiatische Ausrichtung, sowohl vom Interieur, wie auch vom Speisenangebot hat.
Der rote Familienstempel soll sich auch weiterhin im Design finden (muss allerdings nicht unbedingt rot sein).
Ebenso möchten wir das Bild der Mutter aus Ihrer Jungend weiter aufgreifen.
Wir könnten uns ein ähnliches Bild auf den Tischen vorstellen, wie im Anhang zu sehen.
Wir möchten neue Speisekarten für die Abend- und Mittagskarte entwerfen lassen, die gerne mit Skizzen von koreanischem Streetfood untermalt werden sollen.
Wir stellen uns eine Bindung der Speisekarte auf einem Klemmbrett oder durch eine Holzleiste an der Seite (wie bei einem Buch) vor. Hierfür benötigen wir auch entsprechende Papiervorschläge. Wir möchten keine laminierte Speisekarte, eventuell, aber gewachstes, robustes Papier.
Auch bedruckte Tischsets könnten wir uns vorstellen, sowie im weiteren Schritt Essstäbchen mit Gravur oder Druck. Desweiteren wären Papierservietten wünschenswert.
Generell muss ein Spagat zwischen Deutsch und Asiatisch hergestellt werden.
Unsere Typografie ist festgesetzt auf SAUNA SMALL CAPS
wir interessieren uns weiterhin für Poloshirt, Sweater oder Schürzen mit dem neuen CI

```html
<!DOCTYPE html>
<html lang="de">
<head>
<meta charset="utf-8">
<title>Hotel-Restaurant zum Brunnenhof – Visitenkarte</title>
<link rel="stylesheet" href="https://fonts.googleapis.com/css2?family=Josefin+Sans:wght@600;700&family=Oswald:wght@600&display=swap">
<style>
  :root {
    --backdrop: #b5a8a2;
    --card: #f7f7f6;
    --ink: #1c1b1a;
    --copper: #a8643d;
    --muted: #a3a3a3;
    --paper-white: #ffffff;
  }
  * { box-sizing: border-box; margin: 0; padding: 0; }
  html, body { width: 857px; height: 1200px; overflow: hidden; }
  body {
    background: var(--backdrop);
    font-family: "Josefin Sans", sans-serif;
    color: var(--ink);
  }
  .card {
    position: absolute;
    left: 108px;
    width: 640px;
    height: 414px;
    background: var(--card);
    box-shadow: 0 10px 24px rgba(60, 40, 35, 0.25);
    overflow: hidden;
  }
  .card--front { top: 110px; }
  .card--back { top: 640px; }

  .brand {
    display: flex;
    align-items: center;
    justify-content: center;
    gap: 18px;
  }
  .brand__dot {
    width: 22px; height: 22px;
    border-radius: 50%;
    background: var(--copper);
    flex: none;
  }
  .brand__name {
    font-weight: 700;
    text-transform: uppercase;
    text-align: center;
    line-height: 1.2;
    letter-spacing: 0.06em;
  }

  .card--front .brand { height: 100%; }
  .card--front .brand__name { font-size: 30px; color: var(--ink); }

  .back__band {
    position: absolute;
    left: 0; right: 0;
    top: 118px;
    height: 64px;
    background: var(--ink);
  }
  .card--back .brand { position: absolute; left: 0; right: 0; top: 118px; height: 64px; }
  .card--back .brand__name { font-size: 21px; color: var(--paper-white); }

  .contact {
    position: absolute;
    left: 0; right: 0;
    top: 214px;
    text-align: center;
    text-transform: uppercase;
    font-weight: 600;
    color: var(--muted);
    font-size: 13px;
    line-height: 1.3;
    letter-spacing: 0.03em;
  }
  .contact__address { margin-bottom: 12px; }
  .phone {
    position: absolute;
    left: 0; right: 0;
    top: 292px;
    text-align: center;
    font-family: "Oswald", sans-serif;
    font-weight: 600;
    font-size: 62px;
    letter-spacing: 0.12em;
    color: var(--ink);
  }
</style>
</head>
<body>
  <section class="card card--front" aria-label="Vorderseite">
    <div class="brand">
      <span class="brand__dot" aria-hidden="true"></span>
      <p class="brand__name">Hotel-Restaurant<br>zum Brunnenhof</p>
    </div>
  </section>

  <section class="card card--back" aria-label="Rückseite">
    <div class="back__band" aria-hidden="true"></div>
    <div class="brand">
      <span class="brand__dot" aria-hidden="true"></span>
      <p class="brand__name">Hotel-Restaurant zum Brunnenhof</p>
    </div>
    <div class="contact">
      <p class="contact__address">Lindenweg 12,<br>31600 Musterfeld</p>
      <p class="contact__hours">Rezeption / täglich besetzt von:<br>06:00 – 22:00 Uhr</p>
    </div>
    <p class="phone">05123 / 456-0</p>
  </section>
</body>
</html>
```